Judicial election website to attract voters

I need a simple one-page web design for a judicial election. I'm going to put up one picture, maybe two. The picture I have needs a little touch-up (whiten teeth for example). I have 3 paragraphs of text. I'd like a "Donate" button that can link to a CoinDrift account. I'd also like a little background design, like the Constitution or something like that. There's a couple other little things but that's the bulk of it.

Target Market(s)

Involved voters and some media

Industry/Entity Type

Legal

Number of Pages Required

1 page

Font styles to use
Sans Serif

Requirements
Must have
• My picture, text, donate button
• Phrase "Remember to vote August 30, 2016!"
Nice to have
• Perhaps a second photo, maybe a short 30 second video of me talking directly to the voters, cool background: Constitution, something judgey.
Should not have
• Not sure ... profanity, I guess.

```html
<!DOCTYPE html>
<html lang="en">
<head>
<meta charset="utf-8">
<title>Dane Holt for Judge</title>
<link href="https://fonts.googleapis.com/css2?family=Bitter:wght@400;700&family=Lato:wght@300;400;700&display=swap" rel="stylesheet">
<style>
  :root{
    --red:#ee4b4b;
    --red-soft:#e0565b;
    --sky:#16b6ea;
    --blue:#2160c8;
    --ink:#4a4d57;
    --muted:#a9acbb;
    --body:#6a6c74;
    --band:#efeff3;
    --rule:#ececef;
    --white:#ffffff;
  }
  *{margin:0;padding:0;box-sizing:border-box}
  html,body{width:1200px;height:906px;overflow:hidden;background:var(--white)}
  body{position:relative;font-family:'Lato',sans-serif;color:var(--ink)}
  .top-bar{position:absolute;left:0;top:0;width:1200px;height:14px;background:var(--red)}
  .top-photo{position:absolute;left:144px;top:0;width:407px;height:14px;background:linear-gradient(90deg,#3a68b8,#24304c 60%,#1b2233)}
  .avatar{position:absolute;border-radius:50%;background:radial-gradient(circle at 45% 40%,#e9c49a,#b4642a 60%,#6a3a1c)}
  .avatar-lead{left:545px;top:37px;width:106px;height:106px}
  .profile-name{position:absolute;top:178px;left:0;width:1200px;text-align:center;font-weight:300;font-size:24px;letter-spacing:.3px;color:#5a5d66}
  .profile-quote{position:absolute;top:228px;left:216px;width:768px;text-align:center;font-family:'Bitter',serif;font-size:16px;line-height:31px;color:var(--muted)}
  .social{position:absolute;width:54px;height:54px;display:flex;align-items:center;justify-content:center;color:var(--white);font-size:10px;font-weight:700;z-index:2}
  .social-circlo{left:493px;top:312px;background:var(--red-soft)}
  .social-chirpy{left:570px;top:312px;background:var(--sky)}
  .social-kinlink{left:649px;top:305px;background:var(--blue)}
  .social-kinlink::before{content:"";position:absolute;top:-5px;left:22px;border:5px solid transparent;border-top:0;border-bottom-color:var(--blue)}
  .band{position:absolute;left:0;top:339px;width:1200px;height:407px;background:var(--band)}
  .band-art{position:absolute;inset:0;background:linear-gradient(160deg,rgba(255,255,255,.0) 20%,rgba(255,255,255,.55) 55%,rgba(220,220,228,.6) 100%)}
  .endorser-name{position:absolute;top:404px;left:0;width:1200px;text-align:center;font-weight:700;font-size:24px;color:var(--red)}
  .endorser-role{position:absolute;top:457px;left:0;width:1200px;text-align:center;font-size:16px;color:var(--ink)}
  .endorser-quote{position:absolute;top:524px;left:300px;width:600px;text-align:center;font-family:'Bitter',serif;font-size:15px;line-height:30px;color:var(--body)}
  .avatar-thumb{top:644px;width:48px;height:48px}
  .avatar-thumb-left{left:498px}
  .avatar-thumb-right{left:648px}
  .avatar-thumb-active{left:566px;top:637px;width:62px;height:62px;box-shadow:0 3px 8px rgba(0,0,0,.25)}
  .contact{position:absolute;top:782px;display:flex;align-items:center;gap:5px;font-size:15px;color:var(--ink)}
  .contact-email{left:235px;font-weight:300}
  .contact-phone{left:488px}
  .contact-address{left:845px}
  .contact svg{fill:var(--red)}
  .rule{position:absolute;left:147px;top:833px;width:909px;height:1px;background:var(--rule)}
  .donate{position:absolute;left:230px;top:858px;display:flex;align-items:center;gap:6px;font-family:'Bitter',serif;font-weight:700;font-size:22px;color:var(--red);text-decoration:none}
  .donate-dot{width:12px;height:12px;border-radius:50%;background:var(--red)}
  .copyright{position:absolute;right:130px;top:858px;font-size:14px;color:#7c7f88}
</style>
</head>
<body>
  <div class="top-bar"></div>
  <div class="top-photo" role="img" aria-label="Banner photo strip"></div>

  <section class="profile">
    <div class="avatar avatar-lead" role="img" aria-label="Portrait of Dane Holt"></div>
    <h1 class="profile-name">DANE HOLT</h1>
    <p class="profile-quote">Ask any attorney or judge who has worked with Evelyn and they will tell you that she treats every-one with respect and handles courtroom surprises with a calm head and sense of humor.</p>
    <a class="social social-circlo">Circlo</a>
    <a class="social social-chirpy">Chirpy</a>
    <a class="social social-kinlink">Kinlink</a>
  </section>

  <section class="band">
    <div class="band-art" role="img" aria-label="Faint background photo of a supporter waving a flag"></div>
  </section>
  <h2 class="endorser-name">Nora Vale</h2>
  <p class="endorser-role">CEO</p>
  <p class="endorser-quote">She would love your support for judge and the opportunity to use her skills and experience to serve Maple and Cedar County in a new and exciting way.</p>
  <div class="avatar avatar-thumb avatar-thumb-left" role="img" aria-label="Endorser portrait"></div>
  <div class="avatar avatar-thumb-active" role="img" aria-label="Selected endorser portrait"></div>
  <div class="avatar avatar-thumb avatar-thumb-right" role="img" aria-label="Endorser portrait"></div>

  <footer>
    <div class="contact contact-email">
      <svg width="15" height="12" viewBox="0 0 15 12"><path d="M0 0h15v2L7.5 7 0 2z"/><path d="M0 4l7.5 5L15 4v8H0z"/></svg>
      evelyn@votemail.com
    </div>
    <div class="contact contact-phone">
      <svg width="12" height="13" viewBox="0 0 12 13"><path d="M2 0l2.5 3-1.3 1.6c.8 1.8 2.3 3.4 4.2 4.3L9 7.6l3 2.4-1.6 2.5C5 12.5 0 7.5 0 1.6z"/></svg>
      +555 01234 567 &nbsp;-&nbsp; +555 01234 567
    </div>
    <div class="contact contact-address">
      <svg width="13" height="13" viewBox="0 0 13 13"><path d="M13 0L0 5.5l6 1.5 1.5 6z"/></svg>
      24 oak lane - marion
    </div>
    <div class="rule"></div>
    <a class="donate"><span class="donate-dot"></span>CoinDrift donate</a>
    <p class="copyright">— © 2016 by Dane Holt Marlow. All rights reserved. | Privacy Policy |</p>
  </footer>
</body>
</html>
```